Kestrel Facilities Business Card Design

We would now like to design business cards with the new Kestrel Facilities logo

Target Market(s)

Professional

Industry/Entity Type

Professional services

Contact Information for Business Card

Employee name, title, phone number, email address, corporate office address and logo.

Font styles to use
Sans Serif

Colors
0054AA
0677BA
7BADD7
CADEEF
E8F1F8

Requirements
Must have
• My logo
Should not have
• any other pictures or images besides my logo

```html
<!DOCTYPE html>
<html lang="en">
<head>
<meta charset="utf-8">
<title>Kestrel Facilities Business Card</title>
<link rel="stylesheet" href="https://fonts.googleapis.com/css2?family=Arimo:wght@400;700&display=swap">
<style>
  :root {
    --page: #e4e4e4;
    --card: #1f2022;
    --card-deep: #191a1c;
    --blue: #0a78e6;
    --blue-bright: #1a86f0;
    --white: #f2f2f2;
    --silver: #b8b8b8;
    --panel: #2a2b2e;
  }
  * { margin: 0; padding: 0; box-sizing: border-box; }
  html, body { width: 1200px; height: 1200px; overflow: hidden; }
  body {
    background: var(--page);
    font-family: "Arimo", Arial, sans-serif;
    position: relative;
  }
  .card {
    position: absolute;
    left: 262px;
    width: 686px;
    height: 392px;
    background: linear-gradient(135deg, var(--card) 0%, var(--card-deep) 100%);
    overflow: hidden;
  }
  .card-front { top: 165px; }
  .card-back { top: 653px; }

  .decor-panel {
    position: absolute;
    left: 336px; top: 0; right: 0; bottom: 28px;
    background: linear-gradient(160deg, var(--panel) 0%, #222326 70%, var(--card) 100%);
  }
  .brand-name {
    position: absolute;
    left: 47px; top: 72px;
    width: 220px;
    font-weight: 700;
    font-size: 40px;
    line-height: 44px;
    color: var(--blue-bright);
  }
  .person {
    position: absolute;
    right: 51px; top: 196px;
    text-align: right;
  }
  .person-name {
    font-weight: 700;
    font-size: 25px;
    line-height: 28px;
    color: var(--blue-bright);
  }
  .person-title {
    font-size: 17px;
    line-height: 22px;
    color: var(--white);
  }
  .divider {
    position: absolute;
    left: 49px; right: 51px; top: 254px;
    height: 2px;
    background: var(--blue);
  }
  .contact-list {
    position: absolute;
    left: 48px; top: 268px;
    list-style: none;
  }
  .contact-list li {
    display: flex;
    align-items: center;
    gap: 8px;
    font-size: 17.5px;
    line-height: 21.5px;
    color: var(--white);
  }
  .contact-list svg { width: 14px; height: 14px; flex: none; }
  .address {
    position: absolute;
    right: 51px; top: 268px;
    text-align: right;
    font-size: 17.5px;
    line-height: 21.5px;
    color: var(--white);
    font-style: normal;
  }
  .bar {
    position: absolute;
    bottom: 0;
    height: 28px;
  }
  .bar-blue { left: 0; width: 501px; background: linear-gradient(90deg, #0a6fe0, var(--blue-bright)); }
  .bar-grey { left: 547px; right: 0; background: var(--silver); }

  .back-brand {
    position: absolute;
    left: 0; right: 0; top: 50%;
    transform: translateY(-50%);
    text-align: center;
    font-weight: 700;
    font-size: 52px;
    line-height: 58px;
    color: #d9d9d9;
  }
</style>
</head>
<body>
  <section class="card card-front">
    <div class="decor-panel" role="img" aria-label="Faint large brand monogram area"></div>
    <div class="brand-name">Kestrel Facilities</div>

    <div class="person">
      <div class="person-name">DANIEL REYES</div>
      <div class="person-title">President</div>
    </div>

    <div class="divider"></div>

    <ul class="contact-list">
      <li>
        <svg viewBox="0 0 16 16"><path fill="#1a86f0" d="M3.6 1.5l2.3 2.7-1.3 1.8c.9 1.9 2.5 3.5 4.4 4.4l1.8-1.3 2.7 2.3-1.5 2.2C6.6 13.8 2.2 9.4 1.4 3z"/></svg>
        555-014-2730
      </li>
      <li>
        <svg viewBox="0 0 16 16"><rect x="1" y="3.5" width="14" height="9" fill="#1a86f0"/><path d="M1.5 4l6.5 5 6.5-5" stroke="#1f2022" stroke-width="1.3" fill="none"/></svg>
        info@kestrelfacilities.com
      </li>
      <li>
        <svg viewBox="0 0 16 16"><circle cx="8" cy="8" r="7" fill="#1a86f0"/><path d="M4 5c2 0 2 2 4 2s1 3 3 3M9 2.5c-1 1.5 0 2.5 2 2.5" stroke="#1f2022" stroke-width="1.3" fill="none"/></svg>
        kestrelfacilities.com
      </li>
    </ul>

    <address class="address">
      Kestrel Facilities LLC<br>
      1420 Alder Ridge Road<br>
      Alaska 99508
    </address>

    <div class="bar bar-blue"></div>
    <div class="bar bar-grey"></div>
  </section>

  <section class="card card-back">
    <div class="back-brand">Kestrel Facilities</div>
  </section>
</body>
</html>
```